Healthy Food Healthy Brain Rack Card

We want a new 2 page (front and page) 3.67" x 8.5" rack card. This rack card is the first of a series we are creating. We will have five more eventually.

The minimum font size for the text on the front is 11 point and also for other main body text.

Use the text on the word document.

The images and layout in the word document are just sample ideas we had.

We have a subscripton to plivora pics images so prefer to get images from there or free high quality images.

The document is for older readers. Do not put text over graphics and keep it simple and easy to read with high contrast.

We are open to any color scheme, though something that conveys fresh and healthy, is good.

We want some very simple design element(s) incorporated that convey Native American communities or heritage. But NO head dress, teepee graphics, etc.

At the top, of the first page we would like a collage of healthy food images. This can include fish, chicken, fresh vegetables, berries, brown rice, etc.

On the back side, the text below the brown box on the word document with the title "mock up" can be smaller as needed.

Please remember to include the funding statement - it can be in a very small font 6/7 point.

For more information about our project, please visit https://veltronaq.org/mind-care/

```html
<!DOCTYPE html>
<html lang="en">
<head>
<meta charset="utf-8">
<title>Healthy Food, Healthy Brain – Rack Card</title>
<link rel="stylesheet" href="https://fonts.googleapis.com/css2?family=Domine:wght@400;700&family=Raleway:ital,wght@0,400;0,500;0,600;0,700;1,600&display=swap">
<style>
  :root{
    --page:#ece7e1;
    --card:#ffffff;
    --ink:#1f1f1f;
    --brown:#7a2f14;
    --rust:#a8501f;
    --teal:#4a9f9d;
    --band:#c9a48c;
    --shadow:rgba(0,0,0,.22);
    --serif:"Domine", Georgia, serif;
    --sans:"Raleway", Arial, sans-serif;
  }
  *{box-sizing:border-box;margin:0;padding:0}
  html,body{width:720px;height:1200px;overflow:hidden}
  body{background:var(--page);font-family:var(--sans);color:var(--ink);position:relative}
  .rack-card{position:absolute;top:218px;width:330px;height:764px;background:var(--card);box-shadow:0 4px 14px var(--shadow);overflow:hidden}
  .rack-card--front{left:20px}
  .rack-card--back{left:370px}
  .photo{position:absolute}
  .photo--fish{left:0;top:0;width:106px;height:82px;background:linear-gradient(135deg,#d98a3c,#8a5a2c 55%,#5e8a3a)}
  .photo--veg{left:0;top:85px;width:106px;height:84px;background:linear-gradient(135deg,#d63a2a,#e8c23a 45%,#4f8a2e 80%,#6a3a7a)}
  .photo--berries{left:110px;top:10px;width:108px;height:196px;background:linear-gradient(160deg,#2b3450,#c0243a 40%,#2d3558 70%,#b01e34)}
  .photo--chicken{left:222px;top:46px;width:108px;height:78px;background:linear-gradient(135deg,#6a2f17,#b4592a 50%,#3a1d10)}
  .photo--rice{left:222px;top:128px;width:108px;height:82px;background:linear-gradient(180deg,#f2efe9,#d6b77e 55%,#f4f1ec)}
  .photo--jars{left:0;top:640px;width:330px;height:110px;background:linear-gradient(135deg,#e0785a,#f0a48a 40%,#c95a3e 75%,#e7906f)}
  .photo--foil{position:static;width:112px;height:104px;background:linear-gradient(135deg,#c9cdd2,#e89a7a 45%,#6f9a4a 70%,#d8dbe0)}
  .pattern-band{position:absolute;left:0;bottom:0;width:330px;height:14px;background:linear-gradient(180deg,var(--teal) 0 45%,var(--band) 45% 100%)}
  .front-title{position:absolute;left:14px;top:180px;font-family:var(--serif);font-weight:700;color:var(--brown);font-size:20px;line-height:30px}
  .front-title .accent{color:var(--rust)}
  .front-body{position:absolute;left:14px;top:246px;width:306px;font-size:11px;line-height:15px}
  .front-body p{margin-bottom:0}
  .steps-heading{font-weight:600;margin-top:12px;margin-bottom:3px}
  .steps{list-style:none;margin-left:6px}
  .steps li{position:relative;padding-left:8px;margin-bottom:5px}
  .steps li::before{content:"•";position:absolute;left:0}
  .front-body .closing{margin-top:2px}
  .doctor-note{font-family:var(--serif);font-weight:700;color:var(--brown);text-align:center;font-size:12px;line-height:17px;margin-top:6px}
  .quote-box{position:absolute;left:30px;top:668px;width:270px;background:#fff;border:1px solid #e5d6cc;text-align:center;padding:7px 8px;font-size:10px;line-height:14px}
  .quote-box cite{display:block;font-style:normal;font-weight:700;color:var(--brown);margin-top:3px}
  .back-title{position:absolute;left:14px;top:12px;font-family:var(--serif);font-weight:700;color:var(--brown);font-size:19px}
  .recipe{position:absolute;left:14px;top:50px;width:306px;display:flex;gap:12px}
  .recipe-name{font-family:var(--serif);font-weight:700;color:var(--rust);font-size:12px;line-height:17px;margin-bottom:14px}
  .ingredients h3{font-weight:600;color:var(--rust);font-size:12px;margin-bottom:4px}
  .ingredients ul{list-style:none;font-size:11px;line-height:20px;columns:1}
  .ingredients li::before{content:"• "}
  .ing-row{display:flex;gap:20px}
  .ing-note{padding-left:8px;line-height:14px;margin-top:-4px;margin-bottom:2px}
  .method{position:absolute;left:14px;top:236px;width:306px;font-size:11px;line-height:15px;text-align:justify}
  .method em{display:block;font-weight:600;color:var(--rust);margin-top:6px;text-align:left}
  .heritage-note{position:absolute;left:10px;top:362px;width:310px;text-align:center;font-family:var(--serif);font-weight:700;color:var(--brown);font-size:11px;line-height:18px}
  .more-info{position:absolute;left:10px;top:448px;width:310px;text-align:center;font-size:10px;line-height:17px}
  .more-info .label{font-family:var(--serif);font-weight:700;color:var(--rust)}
  .more-info .sub{font-weight:600}
  .more-info .org{font-family:var(--serif);font-weight:700;color:var(--brown)}
  .partner-mark{position:absolute;left:70px;top:640px;display:flex;align-items:center;gap:8px}
  .partner-mark .dot{width:36px;height:36px;border-radius:50%;background:var(--teal)}
  .partner-mark .name{font-family:var(--sans);font-weight:700;color:var(--teal);font-size:14px}
  .funding{position:absolute;left:10px;top:690px;width:312px;font-size:6.5px;line-height:8.4px}
</style>
</head>
<body>
  <section class="rack-card rack-card--front" aria-label="Front of rack card">
    <div class="photo photo--fish" role="img" aria-label="Grilled whole fish on fresh greens"></div>
    <div class="photo photo--veg" role="img" aria-label="Assorted fresh vegetables"></div>
    <div class="photo photo--berries" role="img" aria-label="Blueberries, raspberries and blackberries"></div>
    <div class="photo photo--chicken" role="img" aria-label="Grilled chicken with lemon"></div>
    <div class="photo photo--rice" role="img" aria-label="Bowl of brown rice"></div>

    <h1 class="front-title">Healthy<br>FOOD, <span class="accent">Healthy</span> BRAIN</h1>

    <div class="front-body">
      <p>Everyone slows down as they get older, both in body and mind. Eating healthier food can help your overall health, including brain health.</p>
      <p>It may also reduce your risk for memory loss and problems thinking.</p>
      <p class="steps-heading">Healthier steps to protect your brain:</p>
      <ul class="steps">
        <li>Eat more vegetables, fruits, whole grains, and lower-fat milk</li>
        <li>Use less salt and added sugar</li>
        <li>Eat more fish, chicken, turkey, beans, and nuts</li>
        <li>Cut down on bad fats (“saturated” and trans), cholesterol, and red meat</li>
        <li>Buy fresh, not packaged food when you can</li>
        <li>Limit how much alcohol you drink</li>
        <li>Learn your daily calorie needs for your body size</li>
        <li>Take care of your mental and spiritual health to support your physical and brain health</li>
      </ul>
      <p class="closing">Small changes can make a big difference for better brain health.</p>
      <p class="doctor-note">Talk to your doctor about more steps to healthier food choices.</p>
    </div>

    <div class="photo photo--jars" role="img" aria-label="Jars of preserved salmon"></div>
    <blockquote class="quote-box">
      “Without the elk, salmon, huckleberries, shellfish, and cedar trees we are nobody...”
      <cite>Lorna Whitecedar (Kelvora)</cite>
    </blockquote>
    <div class="pattern-band" role="img" aria-label="Woven border pattern"></div>
  </section>

  <section class="rack-card rack-card--back" aria-label="Back of rack card">
    <h2 class="back-title">Make This at Home</h2>
    <div class="recipe">
      <div>
        <p class="recipe-name">Grilled Salmon<br>and Veggie<br>Foil Packets</p>
        <div class="photo photo--foil" role="img" aria-label="Salmon and vegetables in an open foil packet"></div>
      </div>
      <div class="ingredients">
        <h3>Ingredients:</h3>
        <ul>
          <li class="ing-row"><span>• Salmon</span><span>• Asparagus</span></li>
          <li>Red or Green Peppers</li>
          <li class="ing-note" style="list-style:none">(Or any seasonal vegetable)</li>
          <li class="ing-row"><span>• Onion</span><span>• Lemon – sliced</span></li>
          <li class="ing-row"><span>• Basil</span><span>&nbsp;&nbsp;• Olive Oil</span></li>
          <li>Salt and Pepper</li>
          <li>Garlic Powder</li>
        </ul>
      </div>
    </div>

    <p class="method">Cut asparagus, peppers, and onion into bite-size pieces. Cut salmon into 4-6 oz pieces. Tear tin foil large enough to wrap around salmon &amp; veggies (2 layers). Add veggies and salmon to foil. Drizzle with olive oil, season with salt, pepper, basil, garlic &amp; top with a piece of sliced lemon. Wrap foil tightly around food. Grill at 400 degrees for about 20 minutes.<em>Careful opening!</em></p>

    <p class="heritage-note">Food &amp; drink are a source of strength and connection to community. A return to traditional food pathways and eating local, seasonal fresh foods make healthier eating easier</p>

    <div class="more-info">
      <p class="label">For More Information</p>
      <p class="sub">About Healthier Eating</p>
      <p>PlateWise Guide</p>
      <p>https://www.platewiseguide.org</p>
      <p class="org">About Brain Health</p>
      <p class="org">Tallwater Center for Native Brain Wellness</p>
      <p>https://www.tallwaterbrain.org</p>
      <p class="org">Northfield Memory Care Program</p>
      <p>https://www.northfieldmemory.org/aging</p>
    </div>

    <div class="partner-mark">
      <span class="dot"></span>
      <span class="name">Tallwater Center</span>
    </div>

    <p class="funding">This product is supported by the Halvern Public Health Foundation (HPHF) as part of a financial assistance award totaling $348,711 with 100 percent funded by HPHF. The contents are those of the author(s) and do not necessarily represent the official views of, nor an endorsement, by HPHF or any government agency.</p>
    <div class="pattern-band" role="img" aria-label="Woven border pattern"></div>
  </section>
</body>
</html>
```